Laser Tattoo Removal Business Cards

We are looking for a professional business card design for a laser tattoo removal business. Ideally looking for a black business card design. The name of the business is Brightline Tattoo Removal. We place our cards at local tattoo shops so we ideally are looking for something trendy/edgy to draw both male and female clientele in.

Target Market(s)

Male/Female ages 18-60

Contact Information for Business Card

black background ideally.. hoping to stay within greys, whites and black

Font styles to use
Serif
Sans Serif

Colors
121212
a9a9a9
5c5c5c
f5f5f5
ffffff
7f7f7f
606060
848484
9d9d9d

Requirements
Must have
• Employee Info:
• Melissa Thornbury
• Chief Executive Offer
• m: 919.537.2846
• w: 919.362.4178
• f: 919.685.3907
• mthornbury@brightlinetattooremoval.example
• Address:
• 4615 Oakmere Pkwy, Suite 210
• Raleigh, NC 27654
• Website:
• www.brightlinetattooremoval.example
Nice to have
• Myabe business name on back or logo on back and employee info on the front

```html
<!DOCTYPE html>
<html lang="en">
<head>
<meta charset="utf-8">
<title>Brightline Tattoo Removal – Business Cards</title>
<link rel="stylesheet" href="https://fonts.googleapis.com/css2?family=Roboto:wght@400;500;700&display=swap">
<style>
  :root {
    --backdrop: #3a3431;
    --card: #121212;
    --white: #ffffff;
    --soft-white: #f5f5f5;
    --grey-light: #a9a9a9;
    --grey-mid: #848484;
    --grey-dark: #5c5c5c;
    --rule: #606060;
  }
  * { box-sizing: border-box; margin: 0; padding: 0; }
  html, body { width: 1200px; height: 769px; overflow: hidden; }
  body {
    background: var(--backdrop);
    font-family: "Roboto", Arial, sans-serif;
    color: var(--white);
    position: relative;
  }
  .card {
    position: absolute;
    top: 230px;
    width: 540px;
    height: 309px;
    background: var(--card);
    box-shadow: 0 14px 30px rgba(0,0,0,.45);
    overflow: hidden;
  }
  .card--front { left: 30px; }
  .card--back  { left: 630px; }

  .brand {
    position: absolute;
    text-align: center;
    font-family: "Roboto", Arial, sans-serif;
    font-weight: 500;
    color: var(--white);
    text-transform: uppercase;
    line-height: 1.15;
  }
  .brand__name { font-size: 34px; letter-spacing: 3px; display: block; }
  .brand__sub  { font-size: 15px; letter-spacing: 4px; display: block; margin-top: 6px; }

  .card--front .brand { left: 12px; width: 262px; top: 118px; }
  .card--front .brand__name { font-size: 32px; letter-spacing: 2.5px; }
  .card--front .brand__sub { font-size: 14px; letter-spacing: 3.5px; }

  .divider {
    position: absolute;
    left: 282px; top: 40px;
    width: 1px; height: 200px;
    background: var(--rule);
  }

  .contact {
    position: absolute;
    left: 296px; top: 44px;
    width: 236px;
    font-size: 11px;
    line-height: 1.35;
    color: var(--soft-white);
  }
  .contact__name { font-size: 16px; font-weight: 700; text-transform: uppercase; letter-spacing: .3px; color: var(--white); }
  .contact__title { font-size: 12px; margin-bottom: 8px; }
  .contact__address { margin-bottom: 8px; }
  .contact__list { list-style: none; }
  .contact__list li { display: flex; align-items: center; gap: 6px; white-space: nowrap; font-size: 10px; line-height: 1.5; }
  .contact__list svg { width: 10px; height: 10px; flex: none; fill: var(--soft-white); }

  .edge-band { position: absolute; left: 0; bottom: 0; height: 9px; width: 100%; display: flex; }
  .edge-band__white { width: 68%; background: var(--soft-white); }
  .edge-band__grey  { flex: 1; background: var(--grey-light); }

  .card--back .brand { left: 0; width: 100%; top: 96px; }
  .website {
    position: absolute;
    left: 0; width: 100%; top: 232px;
    text-align: center;
    font-size: 12px;
    letter-spacing: 2.5px;
    color: var(--grey-light);
  }
</style>
</head>
<body>
  <section class="card card--front" aria-label="Business card front">
    <div class="brand">
      <span class="brand__name">Brightline</span>
      <span class="brand__sub">Tattoo Removal</span>
    </div>
    <div class="divider"></div>
    <div class="contact">
      <p class="contact__name">Melissa Thornbury</p>
      <p class="contact__title">Chief Executive Offer</p>
      <p class="contact__address">4615 Oakmere Pkwy, Suite 210<br>Raleigh, NC 27654</p>
      <ul class="contact__list">
        <li><svg viewBox="0 0 10 10"><path d="M2 0.5 L3.6 2.6 L2.7 3.6 Q3.6 5.8 6.4 7.3 L7.4 6.4 L9.5 8 L8.3 9.5 Q3.5 9 0.5 1.7 Z"/></svg>919.362.4178</li>
        <li><svg viewBox="0 0 10 10"><path d="M2.5 0 H7.5 V10 H2.5 Z M3.4 1 V8 H6.6 V1 Z"/></svg>919.537.2846</li>
        <li><svg viewBox="0 0 10 10"><path d="M2.5 0.5 H7.5 V3 H9.5 V8.5 H0.5 V3 H2.5 Z M3.3 1.3 V3 H6.7 V1.3 Z"/></svg>919.685.3907</li>
        <li><svg viewBox="0 0 10 10"><path d="M0.5 2 H9.5 V8.5 H0.5 Z M1.2 2.6 L5 5.5 L8.8 2.6 Z"/></svg>mthornbury@brightlinetattooremoval.example</li>
        <li><svg viewBox="0 0 10 10"><circle cx="5" cy="5" r="4.5"/></svg>www.brightlinetattooremoval.example</li>
      </ul>
    </div>
    <div class="edge-band"><span class="edge-band__white"></span><span class="edge-band__grey"></span></div>
  </section>

  <section class="card card--back" aria-label="Business card back">
    <div class="brand">
      <span class="brand__name">Brightline</span>
      <span class="brand__sub">Tattoo Removal</span>
    </div>
    <p class="website">www.brightlinetattooremoval.example</p>
  </section>
</body>
</html>
```